Child Sponsorship Charity Needs a Wordpress Design

BrightWell GLOBAL is a not-for-profit organization that breaks the cycle of poverty through child sponsorship. We work in 7 countries around the world and are based in Canada. We currently have a Wordpress website and want to update the look and create a more engaging user experience. Our donor base is across Canada and our partners work across the globe. PLEASE SEE THE DESIGN BRIEF ATTACHED. We are looking for out site to be clean, colourful, and inviting. It should maintain our brand image, be welcoming to potential donors, and a great resource to current donors.

Project Deadline Extended Reason: Our Board of Directors wants a chance to provide feedback on the submissions and so we are extending the deadline to give them the opportunity to share their insights. Added Saturday, February 21, 2015

Charity

• Helvetica / Helvetica Neue

• Got a list of colours from the designer who made our logo:
• Brightwell Navy blue
• C: 100
• M: 80
• Y: 0
• K: 23
• Or
• R: 2
• G: 60
• B: 132
• Brightwell lighter blue
• C: 34
• M: 0
• Y: 3
• K: 0
• Or
• R: 161
• G: 221
• B: 241
• Brightwell deep red (newsletter accent colour)
• C: 0
• M: 91
• Y: 88
• K: 30
• Or
• R: 178
• G: 44
• B: 34

```html
<!DOCTYPE html>
<html lang="en">
<head>
<meta charset="utf-8">
<title>BrightWell GLOBAL</title>
<link href="https://fonts.googleapis.com/css2?family=Titillium+Web:wght@400;600;700&family=Open+Sans:wght@400;600&family=Oswald:wght@500&display=swap" rel="stylesheet">
<style>
:root{
  --blue:#0a6aad;
  --blue-dark:#085a94;
  --nav-active:#050505;
  --ink:#111;
  --text:#555;
  --grey-band:#ececec;
  --white:#fff;
  --line:#d9d9d9;
}
*{margin:0;padding:0;box-sizing:border-box}
html,body{width:694px;height:1200px;overflow:hidden;background:var(--white)}
body{position:relative;font-family:"Open Sans",Arial,sans-serif;color:var(--text)}
.abs{position:absolute}
.top-rule{left:0;top:0;width:694px;height:3px;background:var(--blue)}
.brand{left:66px;top:56px;display:flex;align-items:center;gap:8px;font-family:"Titillium Web",sans-serif;font-size:16px;font-weight:400;color:var(--ink);letter-spacing:.2px}
.brand-dot{width:14px;height:14px;border-radius:50%;background:var(--blue)}
.search{left:507px;top:48px;width:120px;height:21px;border:1px solid var(--line);font-size:8px;color:#333;padding:5px 6px}
.search svg{position:absolute;right:5px;top:4px}
.nav{left:0;top:92px;width:694px;height:38px;background:var(--blue);display:flex;padding-left:66px}
.nav a{color:var(--white);text-decoration:none;font-family:"Titillium Web",sans-serif;font-weight:600;font-size:8px;line-height:38px;padding:0 12px}
.nav a.active{background:var(--nav-active);width:59px;text-align:center;padding:0}
.hero{left:0;top:130px;width:694px;height:303px;background:linear-gradient(90deg,#cdbfae 0%,#b9a58f 35%,#6a5a4c 55%,#4b5f8a 72%,#b3a394 100%)}
.hero-title{left:66px;top:255px;font-family:"Oswald",sans-serif;font-weight:500;font-size:36px;color:var(--blue);letter-spacing:.5px}
.arrow{width:20px;height:20px;border-radius:50%;background:#f2f2f2;border:1px solid #bbb;top:268px}
.arrow svg{display:block;margin:4px auto}
.dots-tab{left:304px;top:418px;width:80px;height:15px;background:var(--white);border-radius:8px 8px 0 0;display:flex;justify-content:center;gap:4px;padding-top:4px}
.dot{width:7px;height:7px;border-radius:50%;border:1px solid var(--blue)}
.dot.on{background:var(--blue)}
.welcome-title{left:66px;top:454px;font-family:"Titillium Web",sans-serif;font-size:17px;font-weight:400;color:var(--ink)}
.welcome-title span{color:var(--blue)}
.welcome-copy{left:66px;top:481px;width:328px;font-size:6.5px;line-height:14px;color:#555}
.more{color:var(--blue);font-size:6.5px}
.video{left:398px;top:452px;width:228px;height:146px;border:1px solid var(--line);background:linear-gradient(135deg,#5c8f86,#8b6f5e 55%,#4b3a30)}
.play{left:498px;top:510px;width:28px;height:28px;border-radius:50%;background:#d83a30}
.band{left:0;top:625px;width:694px;height:235px;background:var(--grey-band)}
.section-title{font-family:"Titillium Web",sans-serif;font-size:13px;font-weight:600;color:var(--blue)}
.prog-img{width:178px;height:72px;border:2px solid var(--white);box-shadow:0 0 0 1px var(--line)}
.card-title{font-family:"Titillium Web",sans-serif;font-size:9.5px;font-weight:600;color:var(--ink)}
.card-copy{width:180px;font-size:6.5px;line-height:14px;color:#555}
.btn{background:linear-gradient(#1a7fc4,var(--blue-dark));color:var(--white);font-family:"Titillium Web",sans-serif;font-weight:600;font-size:7px;border-radius:2px;text-align:center}
.sponsor{left:454px;top:656px;width:172px;height:174px;border-radius:4px;background:linear-gradient(160deg,#6d6762,#3e3a37 60%,#5b4c44)}
.sponsor-label{left:454px;top:761px;width:172px;text-align:center;font-family:"Titillium Web",sans-serif;font-weight:700;font-size:15px;color:var(--white)}
.donate-img{left:66px;top:912px;width:176px;height:110px;border:2px solid var(--white);box-shadow:0 0 0 1px var(--line);background:linear-gradient(135deg,#4a3a33,#a14838 50%,#2f4f86)}
.small-copy{font-size:6.5px;line-height:14px;color:#555}
.news-thumb{left:266px;width:55px;height:49px}
.news-head{left:327px;font-size:7px;font-weight:600;color:var(--blue)}
.news-copy{left:327px;width:140px;font-size:5.8px;line-height:10px;color:#555}
.avatar{left:530px;top:917px;width:48px;height:48px;border-radius:50%;background:linear-gradient(#c99a80,#8a5f4a);border:2px solid var(--white);box-shadow:0 0 0 1px var(--line)}
.quote{left:476px;top:973px;width:156px;text-align:center;font-size:6.5px;line-height:14px;color:#555}
.footer{left:0;top:1126px;width:694px;height:74px;background:var(--blue)}
.foot-links{left:66px;top:1143px;font-family:"Titillium Web",sans-serif;font-size:9.5px;color:var(--white)}
.foot-copy{left:66px;top:1164px;font-family:"Titillium Web",sans-serif;font-size:6.5px;color:var(--white)}
.social{top:1154px;width:13px;height:13px;border-radius:2px}
</style>
</head>
<body>
<div class="abs top-rule"></div>
<div class="abs brand"><span class="brand-dot"></span>BrightWell GLOBAL</div>
<div class="abs search">Search
  <svg width="11" height="11" viewBox="0 0 11 11"><circle cx="4.5" cy="4.5" r="3.3" fill="none" stroke="#111" stroke-width="1.5"/><line x1="7" y1="7" x2="10" y2="10" stroke="#111" stroke-width="1.8"/></svg>
</div>
<nav class="abs nav">
  <a class="active" href="#">Home</a><a href="#">Sponsor a Child</a><a href="#">About Us</a><a href="#">Where we Work</a><a href="#">Progrmas</a><a href="#">Get Involved</a><a href="#">Donate</a><a href="#">Blog</a><a href="#">Contatc Us</a>
</nav>

<div class="abs hero" role="img" aria-label="Photo of two smiling boys hugging in a dusty village"></div>
<div class="abs hero-title">BRIGHTWELL</div>
<div class="abs arrow" style="left:31px"><svg width="10" height="10" viewBox="0 0 10 10"><path d="M6.5 2 L3.5 5 L6.5 8" fill="none" stroke="#333" stroke-width="1.6"/></svg></div>
<div class="abs arrow" style="left:643px"><svg width="10" height="10" viewBox="0 0 10 10"><path d="M3.5 2 L6.5 5 L3.5 8" fill="none" stroke="#333" stroke-width="1.6"/></svg></div>
<div class="abs dots-tab"><span class="dot on"></span><span class="dot"></span><span class="dot"></span></div>

<h1 class="abs welcome-title">Welcome To <span>Brightwell Global</span></h1>
<p class="abs welcome-copy">Lorem ipsum dolor sit amet, consectetuer adipiscing elit, sed diam nonummy nibh euismod tincidunt ut laoreet dolore magna aliquam erat volutpat. Ut wisi enim ad minim veniam, quis nostrud exerci tation ullamcorper suscipit lobortis nisl ut aliquip ex ea commodo consequat. Lorem ipsum dolor sit amet, consectetuer adipiscing elit, sed diam nonummy nibh euismod tincidunt ut laoreet dolore magna aliquam erat volutpat. Ut wisi enim ad minim veniam, quis nostrud exerci tation ullamcorper suscipit lobortis nisl ut aliquip ex ea commodo consequat. Lorem ipsum dolor sit amet, consectetuer adipiscing elit, sed diam nonummy nibh or sit amet,<br><span class="more">Read more...</span></p>
<div class="abs video" role="img" aria-label="Video still of smiling children in school uniforms"></div>
<svg class="abs play" viewBox="0 0 28 28"><path d="M11 8 L20 14 L11 20 Z" fill="#fff"/></svg>

<div class="abs band"></div>
<h2 class="abs section-title" style="left:66px;top:647px">Programs</h2>
<div class="abs prog-img" style="left:66px;top:678px;background:linear-gradient(135deg,#6b4a36,#d9d2c8 50%,#5a3d2c)" role="img" aria-label="Photo of young children in white clothes"></div>
<div class="abs prog-img" style="left:255px;top:678px;background:linear-gradient(135deg,#3f4f8f,#3a2a24 50%,#4a5aa0)" role="img" aria-label="Photo of a smiling schoolgirl in a blue uniform"></div>
<div class="abs card-title" style="left:68px;top:757px">Lorem Ipsum Dollar</div>
<p class="abs card-copy" style="left:68px;top:773px">Vivamus porttitor g puttrus nisi eleifend libero a tempus libero lectus feugiat felis Morbi diam</p>
<div class="abs card-title" style="left:256px;top:757px">Lorem Ipsum Dollar</div>
<p class="abs card-copy" style="left:256px;top:773px">Vivamus porttitor g puttrus nisi eleifend libero a tempus libero lectus feugiat felis Morbi diam</p>
<div class="abs btn" style="left:66px;top:810px;width:72px;height:21px;line-height:21px">READ MORE</div>
<div class="abs btn" style="left:255px;top:810px;width:72px;height:21px;line-height:21px">READ MORE</div>
<div class="abs sponsor" role="img" aria-label="Photo of two children on a village path with a sponsorship icon"></div>
<div class="abs sponsor-label">Sponsor a Child</div>

<h2 class="abs section-title" style="left:66px;top:883px">Donate</h2>
<div class="abs donate-img" role="img" aria-label="Photo of a smiling boy in a striped shirt"></div>
<p class="abs small-copy" style="left:66px;top:1026px;width:178px">Lorem ipsum dolor sit amet, consectetuer adipiscing elit, sed diam nonummy nibh euismod tincidunt ut laoreet dolore magna aliquam erat volutpat. Ut wisi enim ad minim veniam.</p>
<div class="abs btn" style="left:66px;top:1086px;width:60px;height:20px;line-height:20px;font-weight:400">Read more...</div>

<h2 class="abs section-title" style="left:266px;top:883px">New &amp; Events</h2>
<div class="abs news-thumb" style="top:912px;background:linear-gradient(#7a5542,#c2785f 60%,#d05a6a)" role="img" aria-label="Photo of a little girl"></div>
<div class="abs news-head" style="top:915px">Lorem ipsum dolor sit</div>
<p class="abs news-copy" style="top:927px">Lorem ipsum dolor sit amet, consectetuer adipiscing elit, sed diam nonummy nibh euismod tincidunt</p>
<div class="abs news-thumb" style="top:973px;background:linear-gradient(#4a3a32,#e6e2dc)" role="img" aria-label="Photo of two children"></div>
<div class="abs news-head" style="top:974px">Lorem ipsum dolor sit</div>
<p class="abs news-copy" style="top:986px">Lorem ipsum dolor sit amet, consectetuer adipiscing elit, sed diam nonummy nibh euismod tincidunt</p>
<div class="abs news-thumb" style="top:1034px;background:linear-gradient(#b0634a,#6a3a2c 60%,#d86a8a)" role="img" aria-label="Photo of a smiling child"></div>
<div class="abs news-head" style="top:1039px">Lorem ipsum dolor sit</div>
<p class="abs news-copy" style="top:1051px">Lorem ipsum dolor sit amet, consectetuer adipiscing elit, sed diam nonummy nibh euismod tincidunt</p>
<div class="abs btn" style="left:402px;top:1086px;width:60px;height:20px;line-height:20px;font-weight:400">Read more...</div>

<h2 class="abs section-title" style="left:515px;top:883px">Testimonials</h2>
<div class="abs avatar" role="img" aria-label="Portrait of the reviewer"></div>
<p class="abs quote">Donec sed odio dui. Nullam id dolor id nibh ultricies vehicula ut id elit. Sollicitudin Lorem Egestas Dapibus. Fusce dapibus, tellus ac cursus commodo</p>
<div class="abs" style="left:476px;top:1034px;width:156px;text-align:center;font-size:8px;color:#777">&ldquo;</div>
<div class="abs" style="left:476px;top:1048px;width:156px;text-align:center;font-size:6px;font-weight:600;color:#222">Mr.Dan, Manager</div>
<div class="abs" style="left:543px;top:1072px;display:flex;gap:4px"><span class="dot on"></span><span class="dot" style="border-color:#333"></span></div>

<footer class="abs footer"></footer>
<div class="abs foot-links">Home &nbsp;|&nbsp; About Us &nbsp;|&nbsp; Serives &nbsp;|&nbsp; Contact Us &nbsp;|&nbsp; Blog</div>
<div class="abs foot-copy">© 2014 Company Name &nbsp;All right reserved &nbsp;Term of Use</div>
<div class="abs social" style="left:557px;background:#3b5a98"></div>
<div class="abs social" style="left:576px;background:#3ab0e2"></div>
<div class="abs social" style="left:595px;background:#1a7bb5"></div>
<div class="abs social" style="left:614px;background:#f39a1e"></div>
</body>
</html>
```